Business Card for a Life Coaching Company

MOSSVALE is a Life Coaching company that was initiated to support people who want to transform thier life or ana aspect of it.
our slogan is : "Dream. Believe. Succeed"
our logo is uploaded.
The name of the company implies that leadership, strength and wisdom required to change your life.
We want an attractive business card that would give an impression of reliability, support and change. so we really want it unique. Here are some examples of unique cards:

http://www.pixelharbornotes.example/2009/05/100-really-creative-business-cards/

MossVale is a life coaching organization focusing on individual transformation through the application of relevant and timeless principles of success.  MossVale believes that real, sustainable life transformations are brought about by tuning into the timeless wisdom we each carry in our hearts while boldy acting in the direction of our dreams.

Contacts on the card:
Address: 7 Tarek Ibn Nabil Heliopolis Cairo Egypt
Tel: +202 24 81 37 52
Fax: +202 24 81 37 19
Mobile: +2 012 574 9026 (Nadia Sherif)
+2 0199915815 (Kamal Rashidi)

By the way, our temporary website is http://www.mossvale.example

We have attached an .eps file with various configurations of our logo.

```html
<!DOCTYPE html>
<html lang="en">
<head>
<meta charset="utf-8">
<title>MossVale Business Card</title>
<link rel="stylesheet" href="https://fonts.googleapis.com/css2?family=Cinzel:wght@400&family=Tinos:wght@400;700&display=swap">
<style>
  :root {
    --page: #ffffff;
    --card-dark: #474546;
    --panel-grey: #7b7b7b;
    --accent: #e8963a;
    --ink-light: #ffffff;
    --label-grey: #b4b4b4;
    --mark-light: #f1f1f1;
    --mark-shade: #bdbdbd;
  }
  * { margin: 0; padding: 0; box-sizing: border-box; }
  html, body { width: 1200px; height: 825px; overflow: hidden; background: var(--page); }
  .canvas { position: relative; width: 1200px; height: 825px; }

  .card {
    position: absolute;
    top: 161px;
    width: 562px;
    height: 336px;
    background: var(--card-dark);
    overflow: hidden;
  }
  .card--front { left: 24px; }
  .card--back { left: 605px; }

  .illustration {
    position: absolute;
    background: linear-gradient(160deg, var(--mark-light) 0%, var(--mark-shade) 55%, var(--card-dark) 100%);
    opacity: 0.85;
  }
  .card--front .illustration { left: 388px; top: 10px; width: 174px; height: 326px; }
  .card--back .illustration { left: 10px; top: 10px; width: 190px; height: 326px; }

  .website {
    position: absolute;
    left: 51px;
    top: 112px;
    font-family: "Cinzel", serif;
    font-size: 19px;
    letter-spacing: 2px;
    color: var(--ink-light);
  }
  .website .website__name { color: var(--accent); }

  .contacts {
    position: absolute;
    left: 51px;
    top: 165px;
    font-family: "Tinos", serif;
    font-size: 15px;
    line-height: 21.5px;
    color: var(--ink-light);
    list-style: none;
  }
  .contacts .label { color: var(--label-grey); }

  .brand-panel {
    position: absolute;
    left: 200px;
    top: 0;
    width: 362px;
    height: 336px;
    background: var(--panel-grey);
    display: flex;
    align-items: center;
    justify-content: center;
  }
  .brand-name {
    font-family: "Tinos", serif;
    font-weight: 400;
    font-size: 46px;
    letter-spacing: 3px;
    color: var(--ink-light);
    white-space: nowrap;
  }
</style>
</head>
<body>
<main class="canvas">
  <section class="card card--front">
    <p class="website">WWW.<span class="website__name">MOSSVALE</span>.COM</p>
    <ul class="contacts">
      <li><span class="label">Tel:</span> +202 24 81 37 52</li>
      <li><span class="label">Fax:</span> +202 24 81 37 19</li>
      <li><span class="label">Mobile:</span> +2 012 574 9026 (Nadia Sherif)</li>
      <li>+2 0196632470 (Kamal Rashidi)</li>
      <li><span class="label">Address:</span> 7 Tarek Ibn Nabil</li>
      <li>Heliopolis Cairo Egypt</li>
    </ul>
    <div class="illustration" role="img" aria-label="Stylised lion head illustration in white and grey, facing left"></div>
  </section>

  <section class="card card--back">
    <div class="illustration" role="img" aria-label="Stylised lion head illustration in white and grey, facing left"></div>
    <div class="brand-panel">
      <h1 class="brand-name">MOSSVALE</h1>
    </div>
  </section>
</main>
</body>
</html>
```